Harborline Renewal Business Card Design

Professional and clean design. The design colors should flow with the logo. Two-sided card with the website on the back which is:

www.HarborlineRenewal.example.

"Specializing in Water Damage Restoration"

On the front I need the name, email, phone, and logo.

Name: Darnell Quisby
Email: Darnell@HarborlineRenewal.example
Phone: 555-318-2046 for now

I only have the Preview and Thumbnail right now but should have the source files uploaded within a day or two.

Target Market(s)

Flood victims, home owners with water damage from busted pipes etc...

Industry/Entity Type

Business

Contact Information for Business Card

Name: Darnell Quisby

Font styles to use
Serif
Sans Serif

Requirements
Must have
• Business Card Details Info

```html
<!DOCTYPE html>
<html lang="en">
<head>
<meta charset="utf-8">
<title>Harborline Renewal Business Card</title>
<link rel="stylesheet" href="https://fonts.googleapis.com/css2?family=Cinzel:wght@400;600&family=Open+Sans:wght@400&display=swap">
<style>
  :root {
    --page: #eef1f3;
    --card: #ffffff;
    --brand-blue: #2b93d1;
    --band-blue: #5bc0ec;
    --circle-blue: #a9dcf5;
    --ink: #2c3a44;
    --shadow: rgba(30, 45, 60, 0.18);
  }
  * { margin: 0; padding: 0; box-sizing: border-box; }
  html, body {
    width: 1200px; height: 1120px; overflow: hidden;
    background: var(--page);
  }
  .sheet {
    position: relative; width: 1200px; height: 1120px;
  }
  .card {
    position: absolute; left: 150px; width: 900px; height: 514px;
    background: var(--card);
    box-shadow: 0 10px 28px var(--shadow);
    overflow: hidden;
  }
  .card--back { top: 26px; }
  .card--front { top: 580px; }

  /* Back side */
  .back-mark {
    position: absolute; left: 40px; top: 50px;
    width: 414px; height: 414px; border-radius: 50%;
    background: var(--circle-blue);
  }
  .back-wordmark {
    position: absolute; left: 500px; top: 200px; width: 370px;
    text-align: center;
    font-family: "Cinzel", serif; font-weight: 600;
    color: var(--brand-blue);
  }
  .back-wordmark .name-main { display: block; font-size: 50px; line-height: 1; letter-spacing: 1px; }
  .back-wordmark .name-sub { display: block; font-size: 22px; letter-spacing: 6px; margin-top: 8px; }

  /* Front side */
  .front-band { position: absolute; inset: 0; }
  .front-mark {
    position: absolute; left: 410px; top: 34px;
    width: 80px; height: 80px; border-radius: 50%;
    background: var(--brand-blue);
  }
  .front-wordmark {
    position: absolute; left: 0; right: 0; top: 130px;
    text-align: center;
    font-family: "Cinzel", serif; font-weight: 600;
    color: var(--brand-blue);
  }
  .front-wordmark .name-main { display: block; font-size: 46px; line-height: 1; letter-spacing: 1px; }
  .front-wordmark .name-sub { display: block; font-size: 18px; letter-spacing: 6px; margin-top: 6px; }
  .holder {
    position: absolute; left: 0; right: 0; top: 232px;
    text-align: center;
    font-family: "Cinzel", serif; font-weight: 400; font-size: 26px;
    color: var(--brand-blue);
  }
  .holder .role { color: var(--ink); }
  .contact {
    position: absolute;
    font-family: "Open Sans", sans-serif; font-size: 20px;
    color: var(--ink);
  }
  .contact--phone { left: 90px; top: 384px; }
  .contact--email { left: 400px; top: 330px; }
  .contact-icon {
    position: absolute; width: 38px; height: 38px; border-radius: 50%;
    background: var(--card);
    display: flex; align-items: center; justify-content: center;
  }
  .contact-icon--phone { left: 118px; top: 334px; }
  .contact-icon--email { left: 604px; top: 282px; }
  .tagline {
    position: absolute; left: 0; right: 0; top: 446px;
    text-align: center;
    font-family: "Cinzel", serif; font-size: 24px; letter-spacing: 1px;
    color: var(--ink);
  }
</style>
</head>
<body>
<main class="sheet">

  <section class="card card--back" aria-label="Card back">
    <div class="back-mark" aria-hidden="true"></div>
    <div class="back-wordmark">
      <span class="name-main">HARBORLINE</span>
      <span class="name-sub">RENEWAL</span>
    </div>
  </section>

  <section class="card card--front" aria-label="Card front">
    <svg class="front-band" width="900" height="514" viewBox="0 0 900 514" aria-hidden="true">
      <polygon points="0,334 900,266 900,514 0,514" fill="var(--band-blue)"/>
    </svg>

    <div class="front-mark" aria-hidden="true"></div>
    <div class="front-wordmark">
      <span class="name-main">HARBORLINE</span>
      <span class="name-sub">RENEWAL</span>
    </div>

    <p class="holder">Darnell Quisby, <span class="role">Title</span></p>

    <div class="contact-icon contact-icon--phone" aria-hidden="true">
      <svg width="20" height="20" viewBox="0 0 24 24">
        <path d="M6.6 10.8a15 15 0 0 0 6.6 6.6l2.2-2.2a1 1 0 0 1 1-.25 11.4 11.4 0 0 0 3.6.57 1 1 0 0 1 1 1V20a1 1 0 0 1-1 1A17 17 0 0 1 3 4a1 1 0 0 1 1-1h3.5a1 1 0 0 1 1 1c0 1.25.2 2.45.57 3.57a1 1 0 0 1-.25 1z" fill="var(--band-blue)"/>
      </svg>
    </div>
    <p class="contact contact--phone">555-318-2046</p>

    <div class="contact-icon contact-icon--email" aria-hidden="true">
      <svg width="20" height="20" viewBox="0 0 24 24">
        <rect x="3" y="6" width="18" height="13" rx="1.5" fill="var(--band-blue)"/>
        <path d="M3.5 7l8.5 6.5L20.5 7" fill="none" stroke="#ffffff" stroke-width="1.6"/>
      </svg>
    </div>
    <p class="contact contact--email">Darnell@HarborlineRenewal.example</p>

    <p class="tagline">Specializing in Water Damage Restoration</p>
  </section>

</main>
</body>
</html>
```